Brandwyn Fuel Retro Website Design

Have a logo. Need a website design to go along with the logo design. Full Design Specs are here: https://files.plinverdocs.net/sheet/d/8QmRtZxWv3-41pk527LNB_XY4HaPcOdsuw2K-rb6/view

Target Market(s)

Independent Gas Station Owners

Number of Pages Required

1 page

Font styles to use
Sans Serif

Colors

Designer to choose colors to be used in the design.

```html
<!DOCTYPE html>
<html lang="en">
<head>
<meta charset="utf-8">
<title>Brandwyn Fuel</title>
<link href="https://fonts.googleapis.com/css2?family=Bitter:wght@400;700&family=Lilita+One&display=swap" rel="stylesheet">
<style>
:root{
  --red:#e3252d;
  --ink:#231f20;
  --paper:#f2f2f2;
  --band:#3a3a3a;
  --muted:#6b6b6b;
  --footer:#231f20;
  --footer-text:#c9c9c9;
  --line:#cfcfcf;
}
*{margin:0;padding:0;box-sizing:border-box}
html,body{width:1200px;height:2377px;overflow:hidden}
body{background:var(--paper);position:relative;font-family:"Bitter",serif;color:var(--ink)}
.abs{position:absolute;white-space:nowrap}

/* header */
.call{left:277px;top:27px;font:19px "Lilita One",sans-serif;letter-spacing:.3px;color:var(--ink)}
.call span{color:var(--red)}
.social{display:flex;gap:7px}
.social i{display:block;width:28px;height:28px;border:1px solid var(--red);border-radius:50%}
.social i.on{background:var(--red)}
.header-social{left:750px;top:24px}
.nav-band{left:180px;top:76px}
.nav-item{top:82px;font:15px "Lilita One",sans-serif;color:#fff;letter-spacing:.8px;text-transform:uppercase}
.nav-item.active{color:var(--red)}
.nav-sep{top:83px;font:13px "Lilita One",sans-serif;color:#bbb}
.brand-circle{left:553px;top:14px;width:94px;height:94px;border-radius:50%;background:var(--band);border:4px solid #fff;box-shadow:0 0 0 2px var(--band)}
.brand-plate{left:538px;top:76px;width:124px;height:34px;background:#fff;border:2px solid var(--band);border-radius:6px;display:flex;align-items:center;justify-content:center;font:700 15px "Bitter",serif;color:var(--ink)}

/* hero */
.hero{left:209px;top:149px;width:782px;height:352px;background:linear-gradient(180deg,#cfccc4 0%,#b3ada2 45%,#6e685f 72%,#4d4942 100%);box-shadow:0 12px 14px -8px rgba(0,0,0,.35)}
.tag{font:18px "Lilita One",sans-serif;padding-left:28px;display:flex;align-items:center;letter-spacing:.5px;text-transform:uppercase}
.tag-red{left:209px;top:397px;width:148px;height:32px;background:var(--red);color:#fff;clip-path:polygon(0 0,100% 0,90% 100%,0 100%)}
.tag-dark{left:209px;top:431px;width:300px;height:34px;background:var(--ink);color:var(--red);clip-path:polygon(0 0,93% 0,100% 100%,0 100%)}
.dots{left:571px;top:521px;display:flex;gap:5px}
.dots i{width:11px;height:11px;border:1.5px solid var(--ink);border-radius:50%}
.dots i.on{background:radial-gradient(var(--ink) 35%,transparent 40%)}

/* intro */
.divider{left:209px;width:782px;height:8px}
.divider::before,.divider::after{content:"";position:absolute;top:0;width:366px;height:8px;border-top:1px solid var(--line);border-bottom:1px solid var(--line)}
.divider::before{left:0}.divider::after{right:0}
.divider b{position:absolute;left:381px;top:-6px;width:20px;height:20px;border-radius:50%;background:var(--red)}
.intro{left:209px;top:601px;width:782px;text-align:center;font:21px/26px "Lilita One",sans-serif;color:var(--red);text-shadow:1.5px 1.5px 0 var(--ink)}

/* services */
.photo{width:262px;height:262px;border-radius:50%;border:1px solid #9a9a9a;box-shadow:inset 0 0 0 7px var(--paper)}
.svc-title{font:22px "Lilita One",sans-serif;color:var(--ink);letter-spacing:.3px}
.svc-title.red{color:var(--red)}
.svc-copy{font:11.2px/17px "Bitter",serif;color:var(--muted)}
.btn{width:124px;height:29px;border:1px solid var(--red);border-radius:14px/15px;display:flex;align-items:center;justify-content:center;font:12.5px "Bitter",serif;color:var(--ink);background:var(--paper)}
.btn.fill{background:var(--red);color:#fff}

/* footer */
.footer{left:0;top:2018px;width:1200px;height:359px;background:var(--footer)}
.cta{left:209px;top:1964px;width:782px;height:106px;background:var(--red);border-radius:26px}
.cta-inner{left:228px;top:1972px;width:744px;height:90px;border:1.5px solid #fff;border-radius:18px}
.cta-text{left:254px;top:2006px;font:18px "Lilita One",sans-serif;color:#fff}
.cta-text span{color:var(--ink)}
.cta-btn{left:834px;top:2004px;width:110px;height:28px;background:var(--ink);color:#fff;font:700 11px "Bitter",serif;display:flex;align-items:center;justify-content:center;clip-path:polygon(0 0,90% 0,100% 50%,90% 100%,0 100%,6% 50%)}
.f-head{top:2122px;font:16px "Lilita One",sans-serif;color:#fff;letter-spacing:.6px;text-transform:uppercase}
.f-red{color:var(--red);font:700 13.5px "Bitter",serif}
.f-text{color:var(--footer-text);font:11.5px/17px "Bitter",serif}
.f-links{top:2160px;list-style:none;color:var(--footer-text);font:11.5px/21.3px "Bitter",serif}
.f-links .on{color:var(--red)}
.subscribe{left:811px;top:2162px;width:180px;height:26px;border-radius:13px;background:#3a3637;color:#9a9a9a;font:10.5px "Bitter",serif;padding:6px 14px}
.footer-social{left:811px;top:2203px}
.footer-social i{width:29px;height:29px}
.rule{left:0;top:2319px;width:1200px;height:1px;background:#3b3738}
.copy{left:209px;top:2339px;font:11.5px "Bitter",serif;color:var(--footer-text)}
.copy span{color:var(--red)}
</style>
</head>
<body>

<!-- header -->
<div class="abs call"><span>Call Us:</span> (555) 214-7630</div>
<div class="abs social header-social" aria-label="Social links"><i></i><i class="on"></i><i></i><i></i><i></i></div>

<svg class="abs nav-band" width="846" height="36" viewBox="0 0 846 36" aria-hidden="true">
  <polygon points="0,4 30,4 30,32 10,32" fill="#4a4a4a"/>
  <polygon points="846,4 816,4 816,32 836,32" fill="#4a4a4a"/>
  <rect x="29" y="0" width="788" height="36" fill="#3a3a3a"/>
  <line x1="29" y1="4" x2="817" y2="4" stroke="#777" stroke-dasharray="3 2"/>
  <line x1="29" y1="32" x2="817" y2="32" stroke="#777" stroke-dasharray="3 2"/>
</svg>
<div class="abs nav-item active" style="left:242px">Home</div>
<div class="abs nav-sep" style="left:302px">//</div>
<div class="abs nav-item" style="left:333px">About</div>
<div class="abs nav-sep" style="left:400px">//</div>
<div class="abs nav-item" style="left:431px">Services</div>
<div class="abs nav-item" style="left:709px">Blog</div>
<div class="abs nav-sep" style="left:767px">//</div>
<div class="abs nav-item" style="left:798px">Review</div>
<div class="abs nav-sep" style="left:870px">//</div>
<div class="abs nav-item" style="left:901px">Contact</div>

<div class="abs brand-circle"></div>
<div class="abs brand-plate">Brandwyn Fuel</div>

<!-- hero -->
<div class="abs hero" role="img" aria-label="Vintage sepia photograph of a fuel depot with delivery trucks and storage tanks"></div>
<div class="abs tag tag-red">Hey There!</div>
<div class="abs tag tag-dark">Welcome to Brandwyn Fuel</div>
<div class="abs dots"><i></i><i class="on"></i><i></i><i></i></div>

<!-- intro -->
<div class="abs divider" style="top:574px"><b></b></div>
<div class="abs intro">Brandwyn Fuel Provides The Full-Scale Service Of A Petroleum Distributor,<br>Delivering Gasoline, Diesel And Lube Oils To Retail</div>
<div class="abs divider" style="top:679px"><b></b></div>

<!-- fuel delivery -->
<div class="abs photo" style="left:302px;top:721px;background:radial-gradient(circle at 45% 55%,#e8e8e8 0,#a9a9a6 40%,#5d5c58 100%)" role="img" aria-label="Photo of white fuel delivery trucks parked on gravel"></div>
<div class="abs svc-title" style="left:634px;top:753px">Fuel Delivery</div>
<div class="abs svc-copy" style="left:634px;top:793px">Brandwyn Fuel provides fuel delivery for<br>independent gas stations, convenience stores, const-<br>ruction sites or any other commercial need.&nbsp; If you<br>are looking for gasoline, high sulfer diesel fuel, farm<br>diesel or other bulk fuel delivered to your business,<br>we will take care of you!</div>
<div class="abs btn" style="left:634px;top:915px">Contact Us</div>

<!-- oil -->
<div class="abs svc-title" style="left:298px;top:1048px">Oil</div>
<div class="abs svc-copy" style="left:298px;top:1089px">Looking for speciality auto, tractor,<br>tractor trailer, aviation or other commercial oils and<br>lubricants Brandwyn Fuel can help!&nbsp; Just call one of our<br>customer oriented staff and we will get what you<br>need quick!&nbsp; We have a complete line of aviation oils<br>and lubricants as well as gear lubricants, greases,<br>oils and more!</div>
<div class="abs btn" style="left:298px;top:1226px">Contact Us</div>
<div class="abs photo" style="left:637px;top:1025px;background:radial-gradient(circle at 55% 60%,#e0c020 0,#c23a55 35%,#2b2a7a 60%,#3a3330 100%)" role="img" aria-label="Photo of colourful fuel cans and jugs on a store shelf"></div>

<!-- farm fuel -->
<div class="abs photo" style="left:302px;top:1328px;background:linear-gradient(180deg,#d9d9d9 0%,#bdbdbd 35%,#9a9a98 60%,#6f6a66 100%)" role="img" aria-label="Photo of a silver fuel tank trailer under bare trees"></div>
<div class="abs svc-title red" style="left:634px;top:1368px">Farm Fuel</div>
<div class="abs svc-copy" style="left:634px;top:1408px">Looking for gasoline, diesel red diesel off road<br>fuel or farm diesel?&nbsp; We can deliver straight to your<br>farm!&nbsp; We can setup your farm tanks, take care<br>of EPA containment and deliver fuel<br>when you need it!</div>
<div class="abs btn fill" style="left:634px;top:1513px">Contact Us</div>

<!-- cargo -->
<div class="abs svc-title" style="left:298px;top:1679px">Cargo Containers</div>
<div class="abs svc-copy" style="left:298px;top:1719px">Want to purchase or lease a storage container,<br>we have what you need!&nbsp; We can deliver or move sto-<br>rage containers to your home, business, construction<br>site or any you need one!</div>
<div class="abs btn" style="left:298px;top:1810px">Contact Us</div>
<div class="abs photo" style="left:637px;top:1632px;background:linear-gradient(160deg,#d4d4d4 0%,#8e9193 40%,#6c7073 70%,#4b4e4f 100%)" role="img" aria-label="Photo of a grey steel cargo storage container"></div>

<!-- footer -->
<div class="abs footer"></div>
<div class="abs cta"></div>
<div class="abs cta-inner"></div>
<div class="abs cta-text"><span>Brandwyn Fuel Makes</span> Customer Service <span>And</span> Satisfaction Priority One!</div>
<div class="abs cta-btn">Contact Us</div>

<div class="abs f-head" style="left:209px">Contact Us</div>
<div class="abs f-red" style="left:209px;top:2158px">Call Us: (555) 214-7630</div>
<div class="abs f-text" style="left:209px;top:2177px">info@brandwyn-fuel.com</div>
<div class="abs f-red" style="left:209px;top:2210px">Address</div>
<div class="abs f-text" style="left:209px;top:2228px">418 Cedar Mill Road, Harlow,<br>TX 75012</div>

<div class="abs f-head" style="left:475px">Quick Links</div>
<ul class="abs f-links" style="left:475px"><li>About</li><li class="on">Services</li><li>Blog</li><li>Review</li><li>Contact</li></ul>

<div class="abs f-head" style="left:642px">Services</div>
<ul class="abs f-links" style="left:642px"><li>Fuel Delivery</li><li>Oil</li><li>Farm Fuel</li><li>Cargo Containers</li></ul>

<div class="abs f-head" style="left:811px">Subscribe Us</div>
<div class="abs subscribe">Enter Your Email...</div>
<svg class="abs" style="left:970px;top:2170px" width="12" height="10" viewBox="0 0 12 10" aria-hidden="true"><polygon points="0,0 12,5 0,10 3,5" fill="#e3252d"/></svg>
<div class="abs social footer-social" aria-label="Social links"><i></i><i class="on"></i><i></i><i></i><i></i></div>

<div class="abs rule"></div>
<div class="abs copy">© 2019 <span>Brandwyn Fuel.</span> All Right Reserved</div>
<svg class="abs" style="left:982px;top:2336px" width="18" height="20" viewBox="0 0 18 20" aria-label="Back to top" role="img"><polygon points="9,0 18,20 9,14 0,20" fill="#e3252d"/></svg>

</body>
</html>
```